Elevating our current Business Card Design

We want to elevate our current business card with a new design to look like a zenith 300 company. We are a premium lubricant distributor (oil and grease).
We need 2 versions, version 1 is as per the uploaded a copy of our current business card with the English version.
For our Chinese version we need to use the front to be English in English and have the back of the card designed exactly like the front for all info to be in Chinese.
The design template needs to be such that we can amend the template with adding different information for each person's card.
The background colour of the card can be changed- we just need to clearly see all information on the card and logos.
The QJR and Ember steady logos cannot have any colour or display changes- only use the logos attached.
All logos need to be included and all information from the attached current card

```html
<!DOCTYPE html>
<html lang="en">
<head>
<meta charset="utf-8">
<title>Orvane Business Card</title>
<link rel="stylesheet" href="https://fonts.googleapis.com/css2?family=Open+Sans:wght@400;600;700;800&family=Montserrat:wght@800&display=swap">
<style>
  :root {
    --stage: #222222;
    --card: #1f1f23;
    --red: #e8291f;
    --red-dark: #9a141a;
    --gold: #f2b21f;
    --orange: #f07a1c;
    --grey: #9a9a9e;
    --white: #ffffff;
  }
  * { box-sizing: border-box; margin: 0; padding: 0; }
  html, body { width: 1200px; height: 780px; overflow: hidden; background: var(--stage); }
  body { position: relative; font-family: "Open Sans", Arial, sans-serif; color: var(--white); }

  .card {
    position: absolute;
    width: 560px; height: 330px;
    background: var(--card);
    border-radius: 18px;
    border-bottom: 4px solid var(--red);
    border-left: 3px solid var(--red);
    box-shadow: 0 18px 40px rgba(0,0,0,.55);
    overflow: hidden;
  }
  .card--front { left: 25px; top: 225px; }
  .card--back  { left: 615px; top: 225px; }

  /* brand stand-in */
  .brand { position: absolute; display: flex; align-items: center; gap: 14px; white-space: nowrap; }
  .brand__dot { border-radius: 50%; background: var(--gold); flex: none; }
  .brand__name { font-weight: 800; color: var(--red); letter-spacing: 2px; line-height: 1; }

  .card--front .brand { left: 120px; top: 84px; }
  .card--front .brand__dot { width: 44px; height: 44px; }
  .card--front .brand__name { font-size: 70px; }

  /* front partner row */
  .partners {
    position: absolute; left: 22px; right: 22px; bottom: 28px;
    display: flex; align-items: center; gap: 12px;
  }
  .ember { display: flex; align-items: center; gap: 6px; font-weight: 700; font-size: 13px; color: var(--white); white-space: nowrap; }
  .ember__dot { width: 14px; height: 14px; border-radius: 50%; background: var(--white); }
  .cert { width: 36px; height: 36px; border-radius: 50%; background: var(--orange); border: 4px solid var(--grey); flex: none; }
  .distributor {
    display: flex; align-items: stretch; height: 46px;
    border: 2px solid var(--red); border-radius: 4px; overflow: hidden;
  }
  .distributor__brand { display: flex; align-items: center; gap: 8px; padding: 0 10px; }
  .distributor__name { font-weight: 800; font-size: 16px; color: var(--red); letter-spacing: 1px; }
  .distributor__tag { font-size: 7.5px; line-height: 1.2; color: var(--red); text-transform: uppercase; font-weight: 600; }
  .supplier { background: var(--red); padding: 6px 12px; display: flex; flex-direction: column; justify-content: center; }
  .supplier__name { font-family: "Montserrat", Arial, sans-serif; font-weight: 800; font-size: 17px; color: #2a0a0a; line-height: 1; }
  .supplier__tag { font-size: 7px; letter-spacing: 1px; color: #5a0c0c; text-transform: uppercase; font-weight: 700; }

  /* back */
  .card--back .brand { left: 30px; top: 128px; gap: 10px; }
  .card--back .brand__dot { width: 24px; height: 24px; }
  .card--back .brand__name { font-size: 34px; letter-spacing: 1px; }

  .divider { position: absolute; left: 252px; top: 70px; width: 2px; height: 140px; background: var(--white); }

  .person { position: absolute; left: 282px; top: 38px; }
  .person__name { font-size: 30px; font-weight: 700; color: var(--red); line-height: 1.05; }
  .person__role { font-size: 14px; font-weight: 600; color: var(--white); margin-bottom: 12px; }

  .contacts { list-style: none; }
  .contacts li { display: flex; align-items: center; gap: 9px; font-size: 13px; line-height: 22px; }
  .contacts svg { width: 13px; height: 13px; fill: var(--red); flex: none; }

  .address { position: absolute; left: 120px; bottom: 70px; font-size: 14px; }
  .bands { position: absolute; left: 0; bottom: 0; width: 560px; height: 70px; }
</style>
</head>
<body>

<section class="card card--front" aria-label="Card front">
  <div class="brand">
    <span class="brand__dot"></span>
    <span class="brand__name">ORVANE</span>
  </div>

  <div class="partners">
    <div class="ember"><span class="ember__dot"></span>Ember steady</div>
    <span class="cert" aria-label="Certification badge"></span>
    <div class="distributor">
      <div class="distributor__brand">
        <span class="distributor__name">ORVANE</span>
        <span class="distributor__tag">Orvane<br>Lubricant<br>Supply</span>
      </div>
      <div class="supplier">
        <span class="supplier__name">KESTREL</span>
        <span class="supplier__tag">Premium Lubricants</span>
      </div>
    </div>
    <span class="cert" aria-label="Certification badge"></span>
    <span class="cert" aria-label="Certification badge"></span>
  </div>
</section>

<section class="card card--back" aria-label="Card back">
  <div class="brand">
    <span class="brand__dot"></span>
    <span class="brand__name">ORVANE</span>
  </div>

  <span class="divider"></span>

  <div class="person">
    <p class="person__name">Mara Tolland</p>
    <p class="person__role">Administration Executive</p>
    <ul class="contacts">
      <li><svg viewBox="0 0 24 24"><path d="M6.6 10.8a15 15 0 0 0 6.6 6.6l2.2-2.2a1 1 0 0 1 1-.25 11 11 0 0 0 3.6.6 1 1 0 0 1 1 1V20a1 1 0 0 1-1 1A17 17 0 0 1 3 4a1 1 0 0 1 1-1h3.5a1 1 0 0 1 1 1 11 11 0 0 0 .6 3.6 1 1 0 0 1-.25 1z"/></svg>1300 472 615</li>
      <li><svg viewBox="0 0 24 24"><path d="M7 1h10a2 2 0 0 1 2 2v18a2 2 0 0 1-2 2H7a2 2 0 0 1-2-2V3a2 2 0 0 1 2-2zm0 3v14h10V4z"/></svg>+61 400 118 204</li>
      <li><svg viewBox="0 0 24 24"><path d="M6 2h9l3 3v4h2a2 2 0 0 1 2 2v9a2 2 0 0 1-2 2H4a2 2 0 0 1-2-2v-9a2 2 0 0 1 2-2h2zm2 2v5h8V6h-2V4zm-1 9v2h2v-2zm4 0v2h2v-2zm4 0v2h2v-2z"/></svg>+61 8 9000 4421</li>
      <li><svg viewBox="0 0 24 24"><path d="M12 2a10 10 0 1 0 0 20 10 10 0 0 0 0-20zm-1 17.9A8 8 0 0 1 4.1 10L9 15v1a2 2 0 0 0 2 2zm6.9-2.5A2 2 0 0 0 16 16h-1v-3a1 1 0 0 0-1-1H8v-2h2a1 1 0 0 0 1-1V7h2a2 2 0 0 0 2-2v-.4a8 8 0 0 1 2.9 12.8z"/></svg>www.orvanedirect.com</li>
      <li><svg viewBox="0 0 24 24"><path d="M2 5h20v14H2zm2 2v.5l8 5 8-5V7zm0 3v7h16v-7l-8 5z"/></svg>mara.tolland@orvanedirect.com</li>
    </ul>
  </div>

  <p class="address">48 Freight Way Ridgeton, WA 6000</p>

  <svg class="bands" viewBox="0 0 560 70" preserveAspectRatio="none" aria-hidden="true">
    <defs>
      <linearGradient id="bandRed" x1="0" x2="1" y1="0" y2="0">
        <stop offset="0" stop-color="#e8291f"/>
        <stop offset="1" stop-color="#9a141a"/>
      </linearGradient>
      <linearGradient id="bandGold" x1="0" x2="1" y1="0" y2="0">
        <stop offset="0" stop-color="#f4c02a"/>
        <stop offset="1" stop-color="#d99a18"/>
      </linearGradient>
    </defs>
    <polygon points="0,46 360,46 380,32 0,32" fill="url(#bandRed)" transform="translate(0,16)"/>
    <polygon points="300,40 560,0 560,18 340,52 320,52" fill="url(#bandGold)"/>
  </svg>
</section>

</body>
</html>
```